Venture 482 - Lumora Book Cover

I am looking for a Lumora book cover for my book about "Venture 482".
The Book is Titled:
Venture 482 Ascended
Shaping Outcomes: Paths To Unlocking Cosmic Truths
Author is Dorian Pell
Here is a book description that may help you understand more about it:
Inspired by the genius of Edwin Marlowe, this comprehensive guide delves into the ancient wisdom and cutting-edge science behind the 482 method, a powerful tool for manifesting your desires. Whether you're seeking personal growth, financial success, or spiritual enlightenment, this book provides advanced techniques and methods to transform your dreams into reality.
Any questions please ask.
Thanks
Owen

```html
<!DOCTYPE html>
<html lang="en">
<head>
<meta charset="utf-8">
<title>Venture 482 Ascended — Dorian Pell</title>
<link rel="stylesheet" href="https://fonts.googleapis.com/css2?family=Bebas+Neue&family=Oswald:wght@200;300;700&display=swap">
<style>
  :root {
    --page-bg: #efeff0;
    --cover-top: #ececee;
    --cover-bottom: #c4c4c8;
    --ink: #1f2147;
    --ink-soft: #2c2f5a;
    --medallion-light: #eef0f6;
    --medallion-mid: #8c93c4;
    --medallion-deep: #27316e;
    --numeral: #1e4a78;
  }
  * { margin: 0; padding: 0; box-sizing: border-box; }
  html, body {
    width: 1200px;
    height: 1131px;
    overflow: hidden;
    background: var(--page-bg);
  }
  .canvas {
    position: relative;
    width: 1200px;
    height: 1131px;
    display: flex;
    align-items: center;
    justify-content: center;
  }
  .book-cover {
    position: relative;
    width: 727px;
    height: 1091px;
    background: radial-gradient(ellipse at 50% 5%, var(--cover-top) 0%, #dcdcdf 45%, var(--cover-bottom) 100%);
    color: var(--ink);
    overflow: hidden;
  }
  .title-word {
    position: absolute;
    top: 72px;
    left: 0;
    width: 100%;
    text-align: center;
    font-family: "Bebas Neue", "Oswald", sans-serif;
    font-size: 100px;
    line-height: 1;
    letter-spacing: 0.01em;
    color: var(--ink);
  }
  .medallion {
    position: absolute;
    left: 64px;
    top: 152px;
    width: 600px;
    height: 600px;
  }
  .title-number {
    position: absolute;
    left: 0;
    top: 400px;
    width: 100%;
    text-align: center;
    font-family: "Oswald", sans-serif;
    font-weight: 300;
    font-size: 96px;
    line-height: 1;
    color: var(--numeral);
  }
  .title-tagline {
    position: absolute;
    top: 746px;
    left: 103px;
    width: 560px;
    font-family: "Bebas Neue", "Oswald", sans-serif;
    font-size: 52px;
    line-height: 1;
    letter-spacing: 1.02em;
    color: var(--ink);
    white-space: nowrap;
  }
  .subtitle {
    position: absolute;
    top: 816px;
    left: 0;
    width: 100%;
    text-align: center;
    font-family: "Oswald", sans-serif;
    text-transform: uppercase;
    color: var(--ink-soft);
  }
  .subtitle-lead {
    display: block;
    font-weight: 700;
    font-size: 24px;
    line-height: 32px;
    color: var(--ink);
  }
  .subtitle-rest {
    display: block;
    font-weight: 300;
    font-size: 20px;
    line-height: 33px;
    letter-spacing: -0.01em;
  }
  .author {
    position: absolute;
    top: 996px;
    left: 0;
    width: 100%;
    text-align: center;
    font-family: "Oswald", sans-serif;
    font-weight: 200;
    font-size: 78px;
    line-height: 1;
    letter-spacing: 0.14em;
    padding-left: 0.14em;
    text-transform: uppercase;
    color: var(--ink);
  }
</style>
</head>
<body>
<main class="canvas">
  <article class="book-cover">
    <h1 class="title-word">Venture</h1>

    <svg class="medallion" viewBox="0 0 600 600" role="img" aria-label="Illustrated mystical medallion: concentric navy and violet rings with sacred geometry, small numerals and radiating rays">
      <defs>
        <radialGradient id="medallion-fill" cx="50%" cy="50%" r="50%">
          <stop offset="0%" stop-color="var(--medallion-light)"/>
          <stop offset="38%" stop-color="#dfe2ee"/>
          <stop offset="55%" stop-color="var(--medallion-mid)"/>
          <stop offset="78%" stop-color="var(--medallion-deep)"/>
          <stop offset="100%" stop-color="var(--medallion-deep)" stop-opacity="0"/>
        </radialGradient>
      </defs>
      <circle cx="300" cy="300" r="285" fill="url(#medallion-fill)"/>
    </svg>

    <p class="title-number" aria-label="482">482</p>

    <p class="title-tagline">Ascended</p>

    <h2 class="subtitle">
      <span class="subtitle-lead">Shaping Outcomes:</span>
      <span class="subtitle-rest">Paths To Unlocking</span>
      <span class="subtitle-rest">Cosmic Truths</span>
    </h2>

    <p class="author">Dorian Pell</p>
  </article>
</main>
</body>
</html>
```